Letterhead for Business Law Firm

We need a letter head for our firm based on the design we have settled on and it is attached. Our clients are small and large businesses around the world, and our letterhead is used typically for formal legal purposes such as demand letters (accusing the recipient of doing bad things) or responding to demand letters. It may also be sent to regulators and other government agencies. So this needs to be tasteful, but a little edgy as well - we try to convey that we are a firm that is different - businesses and investors come to us for creative, quick advice, typically in high stress circumstances, and for our ability to work through high conflict situations, and rapid paced engagements.

Target Market(s)

Lawyers, business executives, investors, government regulators who may receive letters from this firm on behalf of its clients.

Industry/Entity Type

Business

Requirements
Must have
• The design and the firm's contact information:
• Thornwell Law Firm, P.C.
• 1876 NE 57th Ave
• Portland, OR 97213
• phone: 971 555 0147
• fax: 971 555 0182
• in what placement and how depicted (e.g. a phone icon instead of the word "phone") I leave to your creative ideas.
Nice to have
• design and information can be placed at the top, bottom and/or sides of the letter, and the design should be for a standard letter size paper - and can have a separate design for the second page.

```html
<!DOCTYPE html>
<html lang="en">
<head>
<meta charset="utf-8">
<title>Thornwell Law Firm, P.C. — Letterhead</title>
<link href="https://fonts.googleapis.com/css2?family=Source+Sans+3:wght@400;600&display=swap" rel="stylesheet">
<style>
  :root {
    --paper: #ffffff;
    --ink-dark: #231c1e;
    --band-teal: #3e6e7b;
    --band-text: #ffffff;
    --mark-grey: #b9c2c6;
  }
  * { margin: 0; padding: 0; box-sizing: border-box; }
  html, body {
    width: 933px;
    height: 1200px;
    overflow: hidden;
    background: var(--paper);
  }
  .letterhead {
    position: relative;
    width: 933px;
    height: 1200px;
    background: var(--paper);
    font-family: "Source Sans 3", "Myriad Pro", sans-serif;
  }
  .brand {
    position: absolute;
    left: 74px;
    top: 37px;
    height: 68px;
    display: flex;
    align-items: center;
    gap: 14px;
  }
  .brand-square {
    width: 22px;
    height: 22px;
    background: var(--ink-dark);
  }
  .brand-name {
    font-size: 34px;
    font-weight: 400;
    letter-spacing: 9px;
    color: var(--ink-dark);
  }
  .contact-band {
    position: absolute;
    left: 0;
    top: 1138px;
    width: 670px;
    height: 62px;
    background: var(--band-teal);
    color: var(--band-text);
    font-size: 15.5px;
    padding: 8px 0 0 61px;
  }
  .contact-row {
    display: flex;
    align-items: center;
    height: 25px;
    gap: 10px;
    white-space: nowrap;
  }
  .contact-item {
    display: inline-flex;
    align-items: center;
    gap: 4px;
  }
  .contact-item svg {
    width: 14px;
    height: 14px;
    fill: none;
    stroke: var(--band-text);
    stroke-width: 1.6;
  }
  .footer-mark {
    position: absolute;
    left: 670px;
    top: 1138px;
    width: 263px;
    height: 62px;
    background: var(--mark-grey);
    display: flex;
    align-items: center;
    justify-content: center;
  }
  .footer-mark .brand-name {
    font-size: 24px;
    letter-spacing: 6px;
    color: var(--paper);
  }
</style>
</head>
<body>
<main class="letterhead">
  <header class="brand">
    <span class="brand-square"></span>
    <span class="brand-name">THORNWELL</span>
  </header>

  <footer class="contact-band">
    <div class="contact-row">
      <span class="contact-item">
        <svg viewBox="0 0 16 16"><path d="M4 1.5l2.5 3-1.5 1.5c.8 2 2.5 3.7 4.5 4.5l1.5-1.5 3 2.5-1.5 2.5C7 13.5 2.5 9 1.5 3z"/></svg>
        971 555 0147
      </span>
      <span class="contact-item">
        <svg viewBox="0 0 16 16"><rect x="3" y="5" width="10" height="9" rx="1"/><path d="M5 5V1.5h6V5M5.5 8h5M5.5 10.5h5"/></svg>
        971 555 0182
      </span>
      <span class="contact-item">
        <svg viewBox="0 0 16 16"><rect x="1.5" y="3.5" width="13" height="9"/><path d="M1.5 3.5L8 9l6.5-5.5"/></svg>
        info@thornwelllaw.com
      </span>
      <span class="contact-item">
        <svg viewBox="0 0 16 16"><circle cx="8" cy="8" r="6.5"/><path d="M1.5 8h13M8 1.5c-3 3-3 10 0 13M8 1.5c3 3 3 10 0 13"/></svg>
        www.thornwelllaw.com
      </span>
    </div>
    <div class="contact-row">
      <span class="contact-item">
        <svg viewBox="0 0 16 16"><path d="M1.5 14.5h13M2.5 14.5V6L8 2l5.5 4v8.5M5 8h6M5 10.5h6"/></svg>
        1876 NE 57th Ave, Portland, OR 97213
      </span>
    </div>
  </footer>

  <div class="footer-mark">
    <span class="brand-name">THORNWELL</span>
  </div>
</main>
</body>
</html>
```